Business Card Re-Design/Update

We'd like to update out business cards. I've included our current "Style guide" which has the colour scheme of the organisation in it. I've also included the branding files with logos etc in them.

I've also included a copy of one of our existing cards so that you can see how ugly/dated they look. I'd like a fresh modern corporate look.

Target Market(s)

These are for our clients, potential clients, industry contacts - like all business cards

Contact Information for Business Card

Name
Position
Company Address - Level 1, 47 Fernby Street, Carlow Qld 4072
Direct Phone
mobile
Email
Website -www.korvalit.com.au
Logo

Colors

Designer to choose colors to be used in the design.

Requirements
Must have
• Main Logo
• Cards will need to be editable to be able to personalize them for each new employee.
Nice to have
• The MapOut, ShipWell, KeepSteady would be okay to have if they can be sensibly and professionally added to the look without detracting from the main imagery.
• Maybe they could go on the back of the card? will leave this to your creative discretion as to whether/where they fit.
Should not have
• Should not have decorative or script fonts

```html
<!DOCTYPE html>
<html lang="en">
<head>
<meta charset="utf-8">
<title>korvalIT business card</title>
<link rel="stylesheet" href="https://fonts.googleapis.com/css2?family=Asap:wght@400;600;700&display=swap">
<style>
  :root {
    --red-top: #d91c26;
    --red-bottom: #a00f17;
    --ink: #231f20;
    --paper: #ffffff;
    --paper-back: #f1f1f1;
    --stage: #e4e2df;
    --green: #5a9e3a;
    --blue: #1f86c9;
    --magenta: #b61f8f;
    --white-text: #ffffff;
  }
  * { margin: 0; padding: 0; box-sizing: border-box; }
  html, body { width: 1200px; height: 960px; overflow: hidden; }
  body {
    background: var(--stage);
    font-family: "Asap", Arial, sans-serif;
    position: relative;
  }
  .card {
    position: absolute;
    width: 601px;
    height: 342px;
    overflow: hidden;
    box-shadow: 0 3px 8px rgba(0,0,0,0.25);
  }
  .card--front { left: 313px; top: 113px; background: var(--paper); }
  .card--back { left: 311px; top: 472px; background: var(--paper-back); }

  .front-band { position: absolute; inset: 0; width: 601px; height: 342px; }

  .holder { position: absolute; left: 29px; top: 36px; color: var(--white-text); }
  .holder__name { font-size: 19px; font-weight: 700; letter-spacing: 0.1px; }
  .holder__role { font-size: 14px; font-weight: 400; margin-top: 3px; }

  .contact { position: absolute; left: 29px; top: 150px; color: var(--white-text); font-size: 13px; }
  .contact__address { line-height: 18px; margin-bottom: 6px; max-width: 240px; }
  .contact__list { list-style: none; }
  .contact__item { display: flex; align-items: center; height: 19px; }
  .contact__icon { width: 12px; height: 12px; margin-right: 13px; fill: var(--white-text); flex: none; }

  .brand { position: absolute; display: flex; align-items: center; }
  .brand__square { display: block; flex: none; }
  .brand__name { font-weight: 600; line-height: 1; }

  .brand--front { left: 304px; top: 153px; }
  .brand--front .brand__square { width: 26px; height: 26px; background: var(--red-top); margin-right: 10px; }
  .brand--front .brand__name { font-size: 33px; color: var(--ink); }

  .brand--back { left: 300px; top: 140px; }
  .brand--back .brand__square { width: 50px; height: 50px; background: var(--red-top); margin-right: 16px; }
  .brand--back .brand__name { font-size: 56px; color: var(--red-top); }

  .services { position: absolute; left: 32px; top: 168px; list-style: none; }
  .service { display: flex; align-items: center; height: 58px; }
  .service__square { width: 24px; height: 24px; margin-right: 9px; flex: none; }
  .service__name { font-size: 33px; font-weight: 600; line-height: 1; }
  .service--map .service__square { background: var(--green); }
  .service--map .service__name { color: var(--green); }
  .service--ship .service__square { background: var(--blue); }
  .service--ship .service__name { color: var(--blue); }
  .service--keep .service__square { background: var(--magenta); }
  .service--keep .service__name { color: var(--magenta); }
</style>
</head>
<body>
  <svg width="0" height="0" style="position:absolute">
    <defs>
      <linearGradient id="redFade" x1="0" y1="0" x2="0" y2="1">
        <stop offset="0" stop-color="#d91c26"/>
        <stop offset="1" stop-color="#a00f17"/>
      </linearGradient>
      <symbol id="icon-phone" viewBox="0 0 12 12"><path d="M2.4 0.6 L4.2 2.8 L3.2 4.2 Q4.4 6.8 7.8 8.8 L9.2 7.8 L11.4 9.6 L10.2 11.4 Q5.4 11.2 0.6 1.8 Z"/></symbol>
      <symbol id="icon-mobile" viewBox="0 0 12 12"><path d="M3 0 H9 V12 H3 Z M4 1.5 V9.5 H8 V1.5 Z M5.3 10.3 H6.7 V11.2 H5.3 Z" fill-rule="evenodd"/></symbol>
      <symbol id="icon-fax" viewBox="0 0 12 12"><path d="M3 0.5 H9 V3.5 H3 Z M0.5 4.5 H11.5 V9.5 H9.5 V7.5 H2.5 V9.5 H0.5 Z M3 8.5 H9 V11.5 H3 Z"/></symbol>
      <symbol id="icon-mail" viewBox="0 0 12 12"><path d="M0.5 2.5 H11.5 V3.3 L6 6.6 L0.5 3.3 Z M0.5 4.5 L6 7.8 L11.5 4.5 V9.5 H0.5 Z"/></symbol>
      <symbol id="icon-globe" viewBox="0 0 12 12"><circle cx="6" cy="6" r="5.5"/><path d="M1 6 H11 M6 0.5 V11.5" stroke="#a00f17" stroke-width="0.9" fill="none"/></symbol>
    </defs>
  </svg>

  <section class="card card--front" aria-label="Card front">
    <svg class="front-band" viewBox="0 0 601 342" aria-hidden="true">
      <polygon points="0,0 407,0 252,170 412,342 0,342" fill="url(#redFade)"/>
    </svg>

    <div class="holder">
      <p class="holder__name">Maren Holt</p>
      <p class="holder__role">Business Development Manager</p>
    </div>

    <div class="contact">
      <p class="contact__address">Level 1, 47 Fernby Street,<br>Carlow Qld 4072</p>
      <ul class="contact__list">
        <li class="contact__item"><svg class="contact__icon"><use href="#icon-phone"/></svg>+61 (0)7 3000 1482</li>
        <li class="contact__item"><svg class="contact__icon"><use href="#icon-phone"/></svg>+61 (0)7 3000 1495</li>
        <li class="contact__item"><svg class="contact__icon"><use href="#icon-mobile"/></svg>+61 (0)400 123 678</li>
        <li class="contact__item"><svg class="contact__icon"><use href="#icon-fax"/></svg>+61 (0)7 3000 1407</li>
        <li class="contact__item"><svg class="contact__icon"><use href="#icon-mail"/></svg>mholt@korvalit.com.au</li>
        <li class="contact__item"><svg class="contact__icon"><use href="#icon-globe"/></svg>www.korvalit.com.au</li>
      </ul>
    </div>

    <div class="brand brand--front">
      <span class="brand__square" aria-hidden="true"></span>
      <span class="brand__name">korvalIT</span>
    </div>
  </section>

  <section class="card card--back" aria-label="Card back">
    <ul class="services">
      <li class="service service--map"><span class="service__square" aria-hidden="true"></span><span class="service__name">MapOut</span></li>
      <li class="service service--ship"><span class="service__square" aria-hidden="true"></span><span class="service__name">ShipWell</span></li>
      <li class="service service--keep"><span class="service__square" aria-hidden="true"></span><span class="service__name">KeepSteady</span></li>
    </ul>

    <div class="brand brand--back">
      <span class="brand__square" aria-hidden="true"></span>
      <span class="brand__name">korvalIT</span>
    </div>
  </section>
</body>
</html>
```